Front page of Orthodox Christian Monastery Website

I am attaching a couple of versions of design that was already created for the front page of the website. You can grab the same pictures and titles (do not need to know the Russian language) to create your own version of design.
Background: Monastery website contains sermons, stories about monastery life, monastery music of the sisterhood.
Main principles of the design:
1. Various materials/sermons/music have to be clearly visible immediately to the site visitor.
2. Text descriptions to photos should be using font with a good contrast, highly clickable and easily readable.
3. Every article should have a photo or a quality picture (use those in the sample) that will convey something about it.
4. On the top, there will be a menu, which will be a line of words (just use generic words for now).
5. Design should reflect Christian Orthodox themes and fonts.
Updates

Target Market(s)

Orthodox Christian believers around the world and those that are interested in Orthodox Christianity

Number of Pages Required

1 page

Font styles to use
Serif

Colors

Designer to choose colors to be used in the design.

Requirements
Must have
• In the project description
Nice to have
• for some ideas see a popular Orthodox Christian website:
• www.verenskaya-lampada.ru
• We don't want to copy it, but it could give ideas.
Should not have
• Should not be overly complex

```html
<!DOCTYPE html>
<html lang="en">
<head>
<meta charset="utf-8">
<title>Orthodox Christian Monastery</title>
<link rel="stylesheet" href="https://fonts.googleapis.com/css2?family=Open+Sans:wght@400;600&family=Roboto+Condensed:wght@400;700&display=swap">
<style>
:root{
  --red:#8c1111;
  --green:#0e3a32;
  --ink:#1b1b1b;
  --muted:#777;
  --line:#e6e6e6;
  --page:#ffffff;
  --footer:#121212;
  --tag:#222;
  --fb:#2c5a8f;
  --tw:#3fb3e3;
  --rss:#f07a25;
}
*{box-sizing:border-box;margin:0;padding:0}
html,body{width:1200px;height:2473px;overflow:hidden}
body{position:relative;background:var(--page);font-family:"Open Sans",Arial,sans-serif;color:var(--ink)}
.abs{position:absolute}
.topline{left:0;top:0;width:1200px;height:6px;background:var(--green)}
.phone{left:98px;top:46px;font-family:"Roboto Condensed",Arial,sans-serif;font-size:19px;display:flex;align-items:center;gap:10px;white-space:nowrap}
.brand{left:0;width:1200px;top:40px;text-align:center;font-family:"Roboto Condensed",Arial,sans-serif;font-weight:700;font-size:32px;letter-spacing:1px;color:var(--ink);text-transform:uppercase;white-space:nowrap}
.lang{left:996px;top:40px;width:102px;height:36px;border-radius:18px;background:#fff;box-shadow:0 2px 8px rgba(0,0,0,.18);font-size:16px;display:flex;align-items:center;justify-content:center;gap:6px}
.hero{left:0;top:150px;width:1200px;height:504px;background:linear-gradient(180deg,#5b4a3a 0%,#3a4a2c 35%,#2b3a24 65%,#3b5a7a 100%)}
.nav{left:89px;top:117px;width:1023px;height:56px;background:var(--green);display:flex;justify-content:space-between;z-index:2}
.nav a{color:#fff;text-decoration:none;font-size:17px;display:flex;align-items:center;padding:0 32px;white-space:nowrap;flex:none}
.nav a.active{background:var(--red)}
.hero-title{left:0;width:1200px;top:326px;text-align:center;color:#fff;font-family:"Roboto Condensed",Arial,sans-serif;font-weight:400;font-size:54px;white-space:nowrap;text-shadow:0 2px 6px rgba(0,0,0,.5)}
.hero-sub{left:0;width:1200px;top:406px;text-align:center;color:#fff;font-weight:600;font-size:25px;white-space:nowrap;text-shadow:0 2px 6px rgba(0,0,0,.5)}
.hero-arrows{left:1060px;top:596px;display:flex;gap:6px;color:#fff;font-size:20px}
.heading{font-size:23px;font-weight:600;text-transform:uppercase;border-bottom:2px solid var(--red);padding-bottom:10px;white-space:nowrap}
.box{background:#fff;box-shadow:0 1px 6px rgba(0,0,0,.2)}
.photo{position:absolute;overflow:hidden}
.overlay{position:absolute;left:0;right:0;bottom:0;padding:0 22px 12px;background:linear-gradient(0deg,rgba(0,0,0,.75),rgba(0,0,0,0));color:#fff}
.overlay h3{font-weight:400;font-size:19px;margin-bottom:14px;white-space:nowrap}
.meta{display:flex;align-items:center;gap:10px;font-size:12px;color:#ddd;white-space:nowrap}
.meta .right{margin-left:auto;display:flex;gap:10px}
.ico{display:inline-block;width:14px;height:12px;border:1.5px solid currentColor;border-radius:2px}
.ico.round{border-radius:50%;width:12px}
.ico.star{border:none;width:14px;height:14px}
.score{position:absolute;right:0;top:0;width:84px;height:84px;color:#fff;text-align:center;padding-top:10px}
.score b{display:block;font-weight:400;font-size:30px;line-height:1.1}
.score span{font-size:13px}
.list-item{position:absolute;display:flex;gap:22px;border-bottom:1px solid var(--line)}
.thumb{flex:none}
.list-item p{font-size:13px;line-height:1.5;color:#333}
.list-item .meta{color:#888;margin-top:10px;gap:12px}
.track p{font-size:14px;line-height:1.6;color:#333}
.track .date{margin-top:40px;font-size:13px;color:#555;display:flex;align-items:center;gap:10px;white-space:nowrap}
.tags{display:flex;flex-wrap:wrap;gap:6px 6px;padding:25px 18px}
.tags span{background:var(--tag);color:#fff;font-size:13px;padding:8px 19px;white-space:nowrap}
.tags span.on{background:var(--red)}
.social{width:97px;height:115px;color:#fff;text-align:center;font-size:13px;line-height:1.2;padding-top:20px}
.social i{display:block;width:38px;height:38px;border-radius:50%;background:rgba(255,255,255,.25);margin:0 auto 12px}
.footer{left:0;top:2300px;width:1200px;height:173px;background:var(--footer);color:#fff;text-align:center}
.footer nav{margin-top:52px;font-size:15px;word-spacing:2px}
.footer p{margin-top:18px;font-size:14px}
.dots{display:flex;gap:5px}
.dots i{width:8px;height:8px;border-radius:50%;background:#ccc}
.dots i.on{background:#444}
</style>
</head>
<body>
<div class="abs topline"></div>
<div class="abs phone"><svg width="14" height="16" viewBox="0 0 14 16"><path d="M3 1l3 3-2 2c1 2 3 4 5 5l2-2 3 3-2 3C6 14 0 8 1 3z" fill="#8c1111"/></svg>555-010-2247</div>
<div class="abs brand">Orthodox Christian Monastery</div>
<div class="abs lang">English <svg width="9" height="6" viewBox="0 0 9 6"><path d="M1 1l3.5 3.5L8 1" stroke="#111" stroke-width="2" fill="none"/></svg></div>

<div class="abs hero" role="img" aria-label="Sunset view over a forested valley with a blue-domed monastery"></div>
<nav class="abs nav">
  <a class="active" href="#">Portal topics</a>
  <a href="#">Meeting with orthodoxy</a>
  <a href="#">Online magazine</a>
  <a href="#">Questions for the priest</a>
  <a href="#">News</a>
</nav>
<h1 class="abs hero-title">Orthodox Christian Monastery</h1>
<div class="abs hero-sub">Neque porro quisquam est qui dolorem</div>
<div class="abs hero-arrows"><span>‹</span><span>›</span></div>

<h2 class="abs heading" style="left:92px;top:718px;width:689px">Sermons</h2>
<section class="abs box" style="left:94px;top:766px;width:687px;height:638px">
  <div class="photo" style="left:23px;top:23px;width:310px;height:284px;background:linear-gradient(160deg,#c9a568,#7a5a32 60%,#3d2c1c)" role="img" aria-label="Gilded altar with a carved figure of Christ">
    <div class="overlay"><h3>Neque porro quisquam est</h3><div class="meta"><i class="ico"></i>Sermons<span class="right"><i class="ico round"></i><i class="ico"></i><i class="ico"></i></span></div></div>
  </div>
  <div class="photo" style="left:356px;top:23px;width:310px;height:284px;background:linear-gradient(160deg,#2d5aa8,#a83a2a 50%,#3e6a3a)" role="img" aria-label="Stained glass window with biblical figures">
    <div class="overlay"><h3>Neque porro quisquam est</h3><div class="meta"><i class="ico"></i>Sermons<span class="right"><i class="ico round"></i><i class="ico"></i><i class="ico"></i></span></div></div>
  </div>
  <div class="photo" style="left:23px;top:332px;width:310px;height:282px;background:linear-gradient(180deg,#6b6f78,#2a2b30 50%,#141416)" role="img" aria-label="Preacher with raised arms before a lit stage">
    <div class="overlay"><h3>Neque porro quisquam est</h3><div class="meta"><i class="ico"></i>Sermons<span class="right"><i class="ico round"></i><i class="ico"></i></span></div></div>
  </div>
  <div class="photo" style="left:356px;top:332px;width:310px;height:282px;background:linear-gradient(180deg,#6f9bc4,#8a6a4e 45%,#4a3a2e)" role="img" aria-label="Striped monastery church with domes">
    <div class="score" style="background:var(--green)"><b>10</b><span>Amazing</span></div>
    <div class="overlay"><h3>Neque porro quisquam est</h3><div class="meta"><i class="ico"></i>Sermons<span class="right"><i class="ico round"></i><i class="ico"></i><i class="ico"></i></span></div></div>
  </div>
</section>

<h2 class="abs heading" style="left:799px;top:718px;width:312px">Blog post</h2>
<section class="abs box" style="left:798px;top:766px;width:311px;height:638px">
  <div class="list-item" style="left:16px;top:22px;width:278px;height:90px"><div class="thumb" style="width:74px;height:72px;background:linear-gradient(#6d9ad0,#8aa070)" role="img" aria-label="White church under a blue sky"></div><div><p>Ipsum is simply dummy text of the printing and type</p><div class="meta"><svg class="ico star" viewBox="0 0 14 14"><path d="M7 1l2 4 4 .5-3 3 .8 4.5L7 11l-3.8 2 .8-4.5-3-3L5 5z" fill="none" stroke="#888"/></svg><i class="ico"></i><i class="ico round"></i></div></div></div>
  <div class="list-item" style="left:16px;top:118px;width:278px;height:90px"><div class="thumb" style="width:74px;height:72px;background:linear-gradient(#b89a6a,#6a4a2e)" role="img" aria-label="Icon of the Nativity"></div><div><p>Ipsum is simply dummy text of the printing and type</p><div class="meta"><i class="ico"></i><i class="ico round"></i><i class="ico"></i></div></div></div>
  <div class="list-item" style="left:16px;top:214px;width:278px;height:90px"><div class="thumb" style="width:74px;height:72px;background:linear-gradient(#c4b08a,#7a6040)" role="img" aria-label="Carved saint figure"></div><div><p>Ipsum is simply dummy text of the printing and type</p><div class="meta"><svg class="ico star" viewBox="0 0 14 14"><path d="M7 1l2 4 4 .5-3 3 .8 4.5L7 11l-3.8 2 .8-4.5-3-3L5 5z" fill="none" stroke="#888"/></svg><i class="ico"></i><i class="ico round"></i><i class="ico"></i></div></div></div>
  <div class="list-item" style="left:16px;top:310px;width:278px;height:90px"><div class="thumb" style="width:74px;height:72px;background:linear-gradient(#e0a020,#8a4a10)" role="img" aria-label="Golden icon of Christ"></div><div><p>Ipsum is simply dummy text of the printing and type</p><div class="meta"><i class="ico"></i><i class="ico round"></i><i class="ico"></i></div></div></div>
  <div class="list-item" style="left:16px;top:406px;width:278px;height:96px"><div class="thumb" style="width:74px;height:74px;background:linear-gradient(#4a8ad8,#e8e8e8)" role="img" aria-label="Church domes against the sky"></div><div><p>Ipsum is simply dummy text of the printing and type</p><div class="meta"><i class="ico"></i><i class="ico round"></i><i class="ico"></i></div></div></div>
  <div class="list-item" style="left:16px;top:508px;width:278px;height:96px"><div class="thumb" style="width:74px;height:74px;background:linear-gradient(#e8c030,#2a2a2a)" role="img" aria-label="Icon of a bearded saint"></div><div><p>Ipsum is simply dummy text of the printing and type</p><div class="meta"><i class="ico"></i><i class="ico round"></i><i class="ico"></i></div></div></div>
</section>

<h2 class="abs heading" style="left:89px;top:1456px;width:692px">Monastery music of the sisterhood</h2>
<div class="abs dots" style="left:736px;top:1474px"><i></i><i class="on"></i><i></i></div>
<section class="abs box" style="left:92px;top:1500px;width:689px;height:310px">
  <div class="abs track" style="left:22px;top:33px;width:197px"><div style="height:138px;background:linear-gradient(#c8a050,#b01818)" role="img" aria-label="Framed icon on a red altar cloth"></div><p style="margin-top:24px">Ipsum is simply dummy text of the printing and type</p><div class="date"><i class="ico"></i>27 March, 2017</div></div>
  <div class="abs track" style="left:243px;top:33px;width:197px"><div style="height:138px;background:linear-gradient(#5a5a8a,#8a4a3a)" role="img" aria-label="Painted scene of Christ with followers"></div><p style="margin-top:24px">Ipsum is simply dummy text of the printing and type</p><div class="date"><i class="ico"></i>7 March, 2017</div></div>
  <div class="abs track" style="left:463px;top:33px;width:198px"><div style="height:138px;background:linear-gradient(#3a3a3a,#c8a890 60%,#e8e0d8)" role="img" aria-label="Hands folded in prayer over an open book"></div><p style="margin-top:24px">Ipsum is simply dummy text of the printing and type</p><div class="date"><i class="ico"></i>1 January, 2017</div></div>
</section>

<h2 class="abs heading" style="left:800px;top:1456px;width:311px">Christian</h2>
<div class="abs" style="left:1084px;top:1460px;font-size:22px">‹›</div>
<section class="abs box" style="left:798px;top:1498px;width:313px;height:312px">
  <div class="photo" style="left:21px;top:23px;width:270px;height:267px;background:linear-gradient(160deg,#8aa0b8,#b04a3a 55%,#5a6a4a)" role="img" aria-label="Painting of Christ teaching a crowd">
    <div class="overlay" style="padding:0 16px 10px"><h3 style="font-size:16px;margin-bottom:8px">Porro-quisquam est, qui sum</h3><div class="meta"><i class="ico"></i>Sermons</div></div>
  </div>
</section>

<h2 class="abs heading" style="left:93px;top:1840px;width:688px">Stories about monastery</h2>
<section class="abs box" style="left:92px;top:1884px;width:689px;height:375px">
  <div class="photo" style="left:17px;top:39px;width:318px;height:297px;background:linear-gradient(180deg,#9ab0c0,#8a7a5a 50%,#4a3e30)" role="img" aria-label="Statue of Christ with disciples by the sea">
    <div class="score" style="background:#111"><b>8.7</b><span>Awesome</span></div>
    <div class="overlay"><h3 style="font-size:17px">Interview with Maria Lindqvist</h3><div class="meta"><i class="ico"></i>Porro quisquam<span class="right"><i class="ico round"></i><i class="ico"></i><i class="ico"></i></span></div></div>
  </div>
  <div class="list-item" style="left:358px;top:39px;width:310px;height:94px"><div class="thumb" style="width:81px;height:79px;background:linear-gradient(#3a2a1a,#c8b090)" role="img" aria-label="Open Bible on a table"></div><div><p>Ipsum is simply dummy text of the printing and type</p><div class="meta"><svg class="ico star" viewBox="0 0 14 14"><path d="M7 1l2 4 4 .5-3 3 .8 4.5L7 11l-3.8 2 .8-4.5-3-3L5 5z" fill="none" stroke="#888"/></svg><i class="ico"></i><i class="ico round"></i></div></div></div>
  <div class="list-item" style="left:358px;top:141px;width:310px;height:94px"><div class="thumb" style="width:81px;height:79px;background:linear-gradient(#d08a40,#7a2a1a)" role="img" aria-label="Cross against a warm glowing sky"></div><div><p>Ipsum is simply dummy text of the printing and type</p><div class="meta"><i class="ico"></i><i class="ico round"></i><i class="ico"></i></div></div></div>
  <div class="list-item" style="left:358px;top:243px;width:310px;height:94px;border:none"><div class="thumb" style="width:81px;height:79px;background:linear-gradient(#6a8ab0,#2a3a5a)" role="img" aria-label="Person praying in blue light"></div><div><p>Ipsum is simply dummy text of the printing and type</p><div class="meta"><svg class="ico star" viewBox="0 0 14 14"><path d="M7 1l2 4 4 .5-3 3 .8 4.5L7 11l-3.8 2 .8-4.5-3-3L5 5z" fill="none" stroke="#888"/></svg><i class="ico"></i><i class="ico round"></i><i class="ico"></i></div></div></div>
</section>

<h2 class="abs heading" style="left:799px;top:1840px;width:312px">Tags</h2>
<section class="abs box" style="left:798px;top:1882px;width:313px;height:247px">
  <div class="tags"><span>Sermons</span><span>Quisquam</span><span>Sisterhood</span><span>Monastery life</span><span>Dolorem</span><span>portfolio carousel</span><span class="on">Christian</span><span>website plugins</span><span>begginers tutorials</span></div>
</section>
<div class="abs social" style="left:798px;top:2144px;background:var(--fb)"><i></i>259<br>fans</div>
<div class="abs social" style="left:905px;top:2144px;background:var(--tw)"><i></i>568<br>followers</div>
<div class="abs social" style="left:1012px;top:2144px;background:var(--rss)"><i></i>101<br>subscribers</div>

<footer class="abs footer">
  <nav>ABOUT &nbsp;| &nbsp;PRIVACY &nbsp;| &nbsp;TERMS &nbsp;| &nbsp;LEGAL &nbsp;| &nbsp;CONTACT</nav>
  <p>Copyright © 2018 &nbsp;All Rights Reserved</p>
</footer>
</body>
</html>
```